uk based ecommerce website requires fresh look ,high quality look and feel

we are a web based company selling eco friendly ground reinforcement grids to diy and construction sectors
our existing website is www.pondermeshpaths.co.uk ,

we have already updated the logo so that is the branding sorted .so we need a ecommerce website that is very much up-to date in design and layout and which has content management system for ease of use so that we can add products and information as required.

Use current logo as reference for colour scheme.
www.pondermeshpaths.co.uk

The current website has 6 pages accessible through the navigation bar, I would now like 5 pages, removing the need for the Trade Enquiries page possibly have it with along with contact us.

Target Market(s)

construction industry , diy end users,
retail market, landscapers, gardeners

Industry/Entity Type

Construction

Font styles to use
Other font styles liked:
• logo font prometo

Colors
f78f20
9bcb3c

Requirements
Must have
• logo colours and logo design in website with cms responsive design for tablet and mobile devices
• expect content to work flawlessly and look great across all devices
• HTML 5 custom design with coding as required
• must have good experiance in ecommerce website design
• eye catching, high quality look and feel and very user friedly ,very up-to date.
Nice to have
• picture slider show
• explain in writing what exactly i am getting in my ecommerce website
Should not have
• plain , basic design , old fashion looking ,cheap look

```html
<!DOCTYPE html>
<html lang="en">
<head>
<meta charset="utf-8">
<title>Pondermesh Ground Solutions</title>
<link href="https://fonts.googleapis.com/css2?family=Raleway:wght@400;500;600;700&family=Lato:wght@300;400;700&display=swap" rel="stylesheet">
<style>
:root{
  --orange:#f78f20;
  --green:#8cc63f;
  --green-dark:#74ad2b;
  --text:#333333;
  --muted:#8a8a8a;
  --topbar:#e9e9e9;
  --band:#efefef;
  --footer:#8cc63f;
  --footer-dark:#3a3a3a;
  --line:#d9d9d9;
  --white:#ffffff;
}
*{margin:0;padding:0;box-sizing:border-box}
html,body{width:1200px;height:2490px;overflow:hidden}
body{position:relative;background:var(--white);font-family:'Lato',sans-serif;color:var(--text)}
.abs{position:absolute}

.topbar{left:0;top:0;width:1200px;height:42px;background:var(--topbar);font-size:14px;color:#555}
.topbar .phone{left:188px;top:11px;display:flex;align-items:center;gap:8px;color:#222;font-size:15px}
.topbar .account{right:118px;top:12px;display:flex;gap:30px}
.topbar .account span{display:flex;align-items:center;gap:7px}

.header{left:0;top:42px;width:1200px;height:104px;background:var(--white)}
.brand{left:98px;top:22px;width:140px;height:140px;border-radius:50%;background:var(--white);z-index:3;box-shadow:0 2px 6px rgba(0,0,0,.12)}
.brand-name{left:182px;top:62px;z-index:4;font-family:'Raleway',sans-serif;font-weight:700;color:var(--orange);font-size:22px;line-height:24px;letter-spacing:.5px}
.nav{right:120px;top:92px;display:flex;gap:38px;font-family:'Raleway',sans-serif;font-size:15px;font-weight:500;color:#444}
.nav .active{color:var(--green)}

.hero{left:0;top:146px;width:1200px;height:498px;background:linear-gradient(115deg,#5d9a35 0%,#6aa83c 30%,#cfcfcf 38%,#d8d8d8 45%,#e8e8e8 55%,#3f6e22 70%,#2f5a1a 100%)}
.hero-text{left:0;top:306px;width:1200px;text-align:center;color:var(--white);font-family:'Raleway',sans-serif;font-weight:600;text-shadow:0 1px 3px rgba(0,0,0,.35)}
.hero-text h1{font-size:43px;font-weight:600;letter-spacing:.5px;line-height:52px}
.hero-text h2{font-size:30px;font-weight:600;letter-spacing:1px;line-height:40px}
.btn-hero{left:528px;top:415px;width:144px;height:43px;background:var(--orange);color:var(--white);font-size:16px;display:flex;align-items:center;justify-content:center;font-family:'Raleway',sans-serif;font-weight:500}
.dots{left:559px;top:601px;display:flex;gap:4px}
.dots i{width:20px;height:20px;border-radius:50%;background:var(--white);display:block}
.dots i.on{background:#d9b321;border:3px solid var(--white)}

.intro{left:0;top:690px;width:1200px;text-align:center}
.intro h2{font-family:'Raleway',sans-serif;font-weight:500;font-size:24px;letter-spacing:.5px;color:#222}
.intro p{margin:24px auto 0;width:860px;font-size:17px;line-height:34px;color:var(--muted);font-weight:300}

.featured{left:0;top:888px;width:1200px;height:349px;background:var(--band)}
.featured h3{left:113px;top:48px;font-family:'Raleway',sans-serif;font-weight:500;font-size:22px;color:#111}
.arrows{left:1020px;top:58px;display:flex;gap:10px}
.arrows span{width:22px;height:22px;border-radius:50%;background:#d6d6d6;display:flex;align-items:center;justify-content:center}
.product{top:96px;width:476px;height:206px;display:flex}
.product .photo{width:208px;height:206px}
.product .info{flex:1;padding:24px 24px;color:var(--white)}
.product.green .info{background:linear-gradient(180deg,#9bcb3c,#7cb62e)}
.product.orange .info{background:linear-gradient(180deg,#f78f20,#f06d10)}
.product h4{font-family:'Raleway',sans-serif;font-weight:500;font-size:17px;letter-spacing:.3px}
.product p{font-size:10.5px;line-height:17px;margin-top:10px;opacity:.9}
.product .price{font-family:'Raleway',sans-serif;font-size:15px;margin-top:14px}
.product .buy{display:inline-block;margin-top:14px;border:2px solid var(--white);padding:5px 12px;font-size:11px;letter-spacing:.5px}

.section-title{left:0;width:1200px;text-align:center;font-family:'Raleway',sans-serif;font-weight:500;font-size:25px}
.cat-title{top:1312px;color:var(--orange)}
.gal-title{top:1926px;color:#333}
.tile{width:224px;height:220px;border:1px solid var(--line);background:var(--white)}
.tile .photo{width:222px;height:148px}
.tile span{display:block;padding:17px 0 0 24px;font-family:'Raleway',sans-serif;font-weight:500;font-size:15px;line-height:20px;color:#222}

.gallery{left:0;top:1992px;width:1200px;height:174px;display:flex}
.gallery div{flex:1}

.footer{left:0;top:2166px;width:1200px;height:271px;background:var(--footer);color:var(--white)}
.footer h5{font-family:'Raleway',sans-serif;font-weight:500;font-size:20px;margin-bottom:18px}
.footer .col{top:50px;font-size:14px}
.footer li{list-style:none;line-height:31px}
.contact li{display:flex;gap:12px;line-height:20px;margin-bottom:12px;font-size:12.5px}
.email-box{width:262px;height:38px;background:var(--white);color:#999;font-size:13px;display:flex;align-items:center;gap:10px;padding-left:14px;margin-top:16px}
.subscribe{width:94px;height:36px;background:#f7b500;color:var(--white);font-size:13px;display:flex;align-items:center;justify-content:center;margin-top:12px}
.cards{display:flex;gap:12px;margin-top:16px}
.cards span{width:40px;height:24px;background:var(--white);border-radius:2px;color:#555;font-size:8px;font-weight:700;display:flex;align-items:center;justify-content:center}
.bottom{left:0;top:2437px;width:1200px;height:53px;background:var(--footer-dark);color:#ccc;font-size:12px;padding:18px 0 0 125px}
</style>
</head>
<body>

<div class="abs topbar">
  <div class="abs phone">
    <svg width="16" height="16" viewBox="0 0 24 24"><path d="M6.6 10.8a15 15 0 006.6 6.6l2.2-2.2a1 1 0 011-.25 11 11 0 003.6.6 1 1 0 011 1V20a1 1 0 01-1 1A17 17 0 013 4a1 1 0 011-1h3.5a1 1 0 011 1 11 11 0 00.6 3.6 1 1 0 01-.25 1z" fill="none" stroke="#222" stroke-width="1.8"/></svg>
    0800-555-0142
  </div>
  <div class="abs account">
    <span><svg width="12" height="14" viewBox="0 0 12 14"><rect x="1" y="6" width="10" height="8" fill="#444"/><path d="M3 6V4a3 3 0 016 0v2" stroke="#444" stroke-width="1.6" fill="none"/></svg>Register/Login</span>
    <span><svg width="15" height="13" viewBox="0 0 24 21"><path d="M12 21L2 11a6 6 0 019-8l1 1 1-1a6 6 0 019 8z" fill="#444"/></svg>Wishlist</span>
    <span><svg width="20" height="16" viewBox="0 0 24 20"><path d="M1 2h4l3 11h12l3-8H7" stroke="#444" stroke-width="2" fill="none"/><circle cx="10" cy="17" r="2" fill="#444"/><circle cx="18" cy="17" r="2" fill="#444"/></svg>My Cart</span>
  </div>
</div>

<div class="abs header">
  <nav class="abs nav" style="top:50px">
    <span class="active">HOME</span><span>ABOUT US</span><span>GROUND SOLUTIONS</span><span>PONDERMESH</span><span>CONTACT US</span>
  </nav>
</div>
<div class="abs brand"></div>
<div class="abs brand-name">PONDERMESH<br>GROUND SOLUTIONS</div>

<div class="abs hero" role="img" aria-label="Photo of a lawn edge with white pebbles and a round green shrub"></div>
<div class="abs hero-text">
  <h1>CUM SOCIS NATOQUE PENATIBUS</h1>
  <h2>AENEAN PORTTITOR DOLOR</h2>
</div>
<div class="abs btn-hero">VIEW MORE</div>
<div class="abs dots"><i class="on"></i><i></i><i></i><i></i></div>

<section class="abs intro">
  <h2>PONDERMESH ECO SOLUTIONS LTD</h2>
  <p>Stabilised Gravel Paving grids combines purpose designed Cellular reinforcement Pavers with the natural appearance, strength, security and free draining characteristics of a loose aggregate surface</p>
</section>

<section class="abs featured">
  <h3 class="abs">FEATURED PRODUCTS</h3>
  <div class="abs arrows">
    <span><svg width="8" height="10" viewBox="0 0 8 10"><path d="M6 1L2 5l4 4" stroke="#666" stroke-width="1.6" fill="none"/></svg></span>
    <span><svg width="8" height="10" viewBox="0 0 8 10"><path d="M2 1l4 4-4 4" stroke="#666" stroke-width="1.6" fill="none"/></svg></span>
  </div>
  <div class="abs product green" style="left:116px">
    <div class="photo" role="img" aria-label="Photo of a bicycle wheel on a gravel surface" style="background:linear-gradient(160deg,#4a4a4a,#8d8a84 60%,#6b6862)"></div>
    <div class="info">
      <h4>PONDERMESH 25 SYSTEM</h4>
      <p>A justo id velit placerat molestie Donec dictum lectus non odio Cras a ante vitae enim iaculis aliquam Mauris nun</p>
      <div class="price">£ 11.00 EACH</div>
      <span class="buy">BUY NOW</span>
    </div>
  </div>
  <div class="abs product orange" style="left:608px">
    <div class="photo" role="img" aria-label="Photo of truck wheels on black grid panels" style="background:linear-gradient(170deg,#8d8f8c,#5c5d5a 60%,#3a3b39)"></div>
    <div class="info">
      <h4>PONDERMESH 25 SYSTEM</h4>
      <p>A justo id velit placerat molestie Donec dictum lectus non odio Cras a ante vitae enim iaculis aliquam Mauris nun</p>
      <div class="price">£ 11.00 EACH</div>
      <span class="buy">BUY NOW</span>
    </div>
  </div>
</section>

<h3 class="abs section-title cat-title">OUR CATEGORIES</h3>

<div class="abs tile" style="left:116px;top:1379px"><div class="photo" role="img" aria-label="Photo of a geotextile membrane laid on ground" style="background:linear-gradient(180deg,#9fb7c9,#3c3c3c 45%,#2a2a2a)"></div><span>GEOTEXTILE<br>MEMBRANES</span></div>
<div class="abs tile" style="left:364px;top:1379px"><div class="photo" role="img" aria-label="Photo of gravel over black cellular grid" style="background:linear-gradient(180deg,#cfcfcf,#9a9a9a 50%,#2b2b2b)"></div><span>LIGHT DOMESTIC<br>DRIVEWAYS</span></div>
<div class="abs tile" style="left:612px;top:1379px"><div class="photo" role="img" aria-label="Photo of a car wheel on a gravel driveway" style="background:linear-gradient(160deg,#d8d4c6,#b5b0a0 50%,#4b4b4b)"></div><span>HEAVY DOMESTIC<br>DRIVEWAYS</span></div>
<div class="abs tile" style="left:860px;top:1379px"><div class="photo" role="img" aria-label="Photo of a parking area being laid with grid panels" style="background:linear-gradient(180deg,#c9d0d6,#8b7c6a 45%,#3a3a3a)"></div><span>COMMERCIAL<br>PARKING SYSTEM</span></div>
<div class="abs tile" style="left:116px;top:1620px"><div class="photo" role="img" aria-label="Photo of gravel being spread over blue grid" style="background:linear-gradient(180deg,#5b6f8c,#c2a976 50%,#2f4e8a)"></div><span>GEOTEXTILE<br>MEMBRANES</span></div>
<div class="abs tile" style="left:364px;top:1620px"><div class="photo" role="img" aria-label="Photo of an equestrian arena with hills behind" style="background:linear-gradient(180deg,#8fb0c4,#3f6b3a 45%,#c4b89c)"></div><span>LIGHT DOMESTIC<br>DRIVEWAYS</span></div>
<div class="abs tile" style="left:612px;top:1620px"><div class="photo" role="img" aria-label="Photo of grass growing through a grid beside a car" style="background:linear-gradient(180deg,#3e5e2c,#5f8a3b 60%,#87a85a)"></div><span>HEAVY DOMESTIC<br>DRIVEWAYS</span></div>
<div class="abs tile" style="left:860px;top:1620px"><div class="photo" role="img" aria-label="Photo of grass grid panels on a lawn" style="background:linear-gradient(180deg,#4d6e3a,#6e9152 50%,#3e5a2e)"></div><span>COMMERCIAL<br>PARKING SYSTEM</span></div>

<h3 class="abs section-title gal-title">OUR GALLERY</h3>
<div class="abs gallery">
  <div role="img" aria-label="Photo of a vehicle wheel on gravel" style="background:linear-gradient(160deg,#d9d5c8,#6d6c68 60%,#3a3a3a)"></div>
  <div role="img" aria-label="Photo of close-up black grid panel" style="background:linear-gradient(160deg,#6a6a6a,#2e2e2e 60%,#8a8a8a)"></div>
  <div role="img" aria-label="Photo of a site with red barriers and a cone" style="background:linear-gradient(180deg,#9fb8cc,#2e2e2e 50%,#b63a2e)"></div>
  <div role="img" aria-label="Photo of gravel spread over a blue grid" style="background:linear-gradient(180deg,#4d6c9a,#c2a976 55%,#2f4e8a)"></div>
  <div role="img" aria-label="Photo of a blue hexagonal grid close-up" style="background:linear-gradient(160deg,#e7ebf2,#5e7ab8 55%,#2d4f99)"></div>
</div>

<footer class="abs footer">
  <div class="abs col contact" style="left:125px">
    <h5>Contact Us</h5>
    <ul>
      <li><svg width="14" height="18" viewBox="0 0 14 18"><path d="M7 17s6-6 6-10A6 6 0 001 7c0 4 6 10 6 10z" stroke="#fff" stroke-width="1.5" fill="none"/><circle cx="7" cy="7" r="2" fill="#fff"/></svg><span>12 Fenwick Lane Unit 4<br>LS9 4QT Voice 0113 496 0781</span></li>
      <li><svg width="14" height="14" viewBox="0 0 24 24"><path d="M6.6 10.8a15 15 0 006.6 6.6l2.2-2.2a1 1 0 011-.25 11 11 0 003.6.6 1 1 0 011 1V20a1 1 0 01-1 1A17 17 0 013 4a1 1 0 011-1h3.5a1 1 0 011 1 11 11 0 00.6 3.6 1 1 0 01-.25 1z" fill="none" stroke="#fff" stroke-width="2"/></svg><span>Phone:+44 113 496 0325</span></li>
      <li><svg width="16" height="12" viewBox="0 0 16 12"><rect x="1" y="1" width="14" height="10" stroke="#fff" stroke-width="1.4" fill="none"/><path d="M1 1l7 6 7-6" stroke="#fff" stroke-width="1.4" fill="none"/></svg><span>info@pondermeshpaths.co.uk</span></li>
    </ul>
  </div>
  <div class="abs col" style="left:365px">
    <h5>Sublinks</h5>
    <ul><li>About Us</li><li>Why Choose Us</li><li>Our Wine</li><li>Shop Now</li></ul>
  </div>
  <div class="abs col" style="left:520px;top:46px">
    <h5>Resources</h5>
    <ul><li>FAQ</li><li>Support</li><li>Term of Use</li><li>Contact Us</li></ul>
  </div>
  <div class="abs col" style="left:662px;top:46px">
    <h5>Social</h5>
    <ul>
      <li style="display:flex;align-items:center;gap:8px"><svg width="22" height="22"><circle cx="11" cy="11" r="10" stroke="#fff" stroke-width="1.4" fill="none"/></svg>Friendsbook</li>
      <li style="display:flex;align-items:center;gap:8px"><svg width="22" height="22"><circle cx="11" cy="11" r="10" stroke="#fff" stroke-width="1.4" fill="none"/></svg>Chirper</li>
      <li style="display:flex;align-items:center;gap:8px"><svg width="22" height="22"><circle cx="11" cy="11" r="10" stroke="#fff" stroke-width="1.4" fill="none"/></svg>Circlesphere</li>
    </ul>
  </div>
  <div class="abs col" style="left:818px">
    <h5 style="margin-bottom:10px">Join Our Newsletter</h5>
    <div>Please sign up for our news</div>
    <div class="email-box"><svg width="16" height="12" viewBox="0 0 16 12"><rect width="16" height="12" fill="#aaa"/><path d="M0 0l8 6 8-6" stroke="#fff" stroke-width="1.2" fill="none"/></svg>Email address</div>
    <div class="subscribe">SUBSCRIBE</div>
    <div class="cards"><span>Cardex</span><span>Paywell</span><span>Orbit</span><span>Meridian</span><span>Payline</span></div>
  </div>
</footer>
<div class="abs bottom">© 2016 Company Name &nbsp;All right reserved</div>

</body>
</html>
```